Quenvale Capital LLC

Need Professional Business cards for New Investment Fund

Target Market(s)

High Quality investors

Industry/Entity Type

Financial

Contact Information for Business Card

Phone Number +1 555 284 6190
Name Lukas Varenko
Title Fund Manager
email lv@FundQuenvale.com
Website www.FundQuenvale.com

Colors

Designer to choose colors to be used in the design.

Requirements
Must have
• Must have our Logo and all of the above. Must be made so lettering and loge can be raised

```html
<!DOCTYPE html>
<html lang="en">
<head>
<meta charset="utf-8">
<title>Quenvale Capital LLC — Business Card</title>
<link href="https://fonts.googleapis.com/css2?family=Raleway:wght@400;500;700&display=swap" rel="stylesheet">
<style>
  :root {
    --backdrop: #1c1c1d;
    --card: #121316;
    --green: #5cbf48;
    --white: #ffffff;
    --text-soft: #e6e6e6;
    --muted: #5d6a5a;
  }
  html, body {
    margin: 0;
    padding: 0;
    width: 1200px;
    height: 900px;
    overflow: hidden;
    background: var(--backdrop);
    font-family: "Raleway", Arial, sans-serif;
  }
  .canvas {
    position: relative;
    width: 1200px;
    height: 900px;
  }
  .card {
    position: absolute;
    left: 250px;
    width: 700px;
    height: 400px;
    background: var(--card);
    overflow: hidden;
    box-shadow: 0 18px 40px rgba(0,0,0,0.55);
  }
  .card--back { top: 35px; }
  .card--front { top: 465px; }

  /* Back side */
  .back-brand {
    position: absolute;
    left: 190px;
    top: 222px;
    display: flex;
    align-items: center;
    gap: 10px;
    font-weight: 700;
    font-size: 26px;
    letter-spacing: 1px;
    color: var(--muted);
  }
  .back-mark {
    width: 16px;
    height: 16px;
    background: var(--muted);
  }
  .back-bar {
    position: absolute;
    left: 420px;
    right: 0;
    top: 232px;
    height: 18px;
    background: var(--green);
  }

  /* Front side */
  .brand {
    position: absolute;
    left: 60px;
    top: 176px;
    display: flex;
    align-items: center;
    gap: 10px;
    font-weight: 700;
    font-size: 30px;
    letter-spacing: 0.5px;
    color: var(--white);
  }
  .brand-mark {
    width: 18px;
    height: 18px;
    background: var(--green);
  }
  .divider {
    position: absolute;
    left: 322px;
    top: 118px;
    width: 2px;
    height: 150px;
    background: var(--green);
  }
  .contact {
    position: absolute;
    left: 350px;
    top: 120px;
  }
  .contact-name {
    margin: 0;
    font-weight: 700;
    font-size: 24px;
    letter-spacing: 1.5px;
    text-transform: uppercase;
    color: var(--white);
  }
  .contact-title {
    margin: 4px 0 14px;
    font-weight: 500;
    font-size: 19px;
    letter-spacing: 0.5px;
    color: var(--text-soft);
  }
  .contact-list {
    list-style: none;
    margin: 0;
    padding: 0;
  }
  .contact-item {
    display: flex;
    align-items: center;
    gap: 12px;
    font-size: 19px;
    letter-spacing: 0.4px;
    color: var(--text-soft);
    line-height: 30px;
  }
  .contact-icon {
    width: 16px;
    height: 16px;
    flex: none;
  }
</style>
</head>
<body>
<main class="canvas">

  <section class="card card--back" aria-label="Card back">
    <div class="back-brand">
      <span class="back-mark"></span>
      <span class="back-name">QUENVALE</span>
    </div>
    <div class="back-bar"></div>
  </section>

  <section class="card card--front" aria-label="Card front">
    <div class="brand">
      <span class="brand-mark"></span>
      <span class="brand-name">QUENVALE</span>
    </div>
    <div class="divider"></div>
    <div class="contact">
      <h1 class="contact-name">Lukas Varenko</h1>
      <p class="contact-title">Title Fund Manager</p>
      <ul class="contact-list">
        <li class="contact-item">
          <svg class="contact-icon" viewBox="0 0 16 16" aria-hidden="true">
            <path d="M3 1.5l2.5 0 1 3.5-1.6 1.2c.8 1.8 2.2 3.2 4 4l1.2-1.6 3.4 1v2.6c0 .8-.7 1.3-1.5 1.2C6.6 12.8 2.8 9 2 3c-.1-.8.3-1.5 1-1.5z" fill="var(--green)"/>
          </svg>
          +1 555 284 6190
        </li>
        <li class="contact-item">
          <svg class="contact-icon" viewBox="0 0 16 16" aria-hidden="true">
            <rect x="1" y="3" width="14" height="10" fill="none" stroke="var(--green)" stroke-width="1.5"/>
            <path d="M1.5 3.5L8 9l6.5-5.5" fill="none" stroke="var(--green)" stroke-width="1.5"/>
          </svg>
          lv@FundQuenvale.com
        </li>
        <li class="contact-item">
          <svg class="contact-icon" viewBox="0 0 16 16" aria-hidden="true">
            <circle cx="8" cy="8" r="6.5" fill="none" stroke="var(--green)" stroke-width="1.4"/>
            <ellipse cx="8" cy="8" rx="3" ry="6.5" fill="none" stroke="var(--green)" stroke-width="1.2"/>
            <path d="M1.5 8h13M2.5 4.8h11M2.5 11.2h11" stroke="var(--green)" stroke-width="1.1"/>
          </svg>
          www.FundQuenvale.com
        </li>
      </ul>
    </div>
  </section>

</main>
</body>
</html>
```